Quarrybend Marble & Tile Needs a Business Card

Attached you will find your logo, my photo and design guidelines for a new business card. The final design will need two separate files to create an embossed card. The cards will be printed by www.plinkprint.com (Instructions below)
Format is the Plink SQUARE card
Quarrybend Marble And Tile is a brick and mortar, retail stone and tile shop.
One the front:
Quarrybend Marble And Tile
Dorian Fesslock
Owner
24807 Hollis Verdant Blvd
Suite P & R
Charlotte, NC 28193
Cell: 704-583-7142
Web: www.QuarrybendMarbleAndTile.com
(Make each word of the domain a different or alternating color)
On the back;
Something that shows beautiful colorful tile
Follow the design guide closely please. For more information see this page that describes creating the spot gloss file: https://www.plinkprint.com/us/business-cards/design-guidelines-spot-gloss
The logo is what we would like to have raised spot glossed.
Format is the Plink SQUARE card. See attahced guidlines.

```html
<!DOCTYPE html>
<html lang="en">
<head>
<meta charset="utf-8">
<title>Quarrybend Marble &amp; Tile — Square Business Card</title>
<link rel="stylesheet" href="https://fonts.googleapis.com/css2?family=Raleway:wght@400;500&family=Tinos:wght@400;700&display=swap">
<style>
  :root {
    --page: #c4c5c7;
    --card: #000000;
    --white: #ffffff;
    --gold: #d0922e;
    --slate: #34434d;
    --stone: #8c8575;
    --rust: #c2582c;
    --tile-rust: rgba(194, 88, 44, 0.16);
    --tile-slate: rgba(70, 96, 110, 0.2);
    --tile-gold: rgba(208, 146, 46, 0.13);
    --tile-sage: rgba(120, 132, 110, 0.14);
  }
  * { margin: 0; padding: 0; box-sizing: border-box; }
  html, body { width: 1200px; height: 900px; overflow: hidden; }
  body { background: var(--page); position: relative; font-family: "Raleway", sans-serif; }

  .card { position: absolute; background: var(--card); overflow: hidden; }
  .card--front { left: 109px; top: 217px; width: 465px; height: 467px; }
  .card--back { left: 623px; top: 215px; width: 464px; height: 469px; }

  .brand { position: absolute; display: flex; align-items: center; }
  .brand-square { background: var(--gold); flex: none; }
  .brand-name {
    font-family: "Raleway", sans-serif; font-weight: 500;
    line-height: 1.2; white-space: nowrap;
  }

  /* front */
  .brand--front { left: 50px; top: 68px; gap: 26px; }
  .brand--front .brand-square { width: 82px; height: 82px; }
  .brand--front .brand-name { color: var(--slate); font-size: 24px; letter-spacing: 0.2em; }

  .person { position: absolute; left: 46px; top: 245px; }
  .person-name { font-family: "Tinos", serif; font-weight: 700; color: var(--white); font-size: 24px; line-height: 1; }
  .person-title {
    display: inline-block; margin-top: 5px; padding-bottom: 2px;
    color: var(--gold); font-size: 15px; border-bottom: 1px solid var(--gold);
  }

  .portrait {
    position: absolute; left: 45px; top: 308px; width: 104px; height: 104px;
    border: 2px solid var(--gold); padding: 3px;
  }
  .portrait-fill { width: 100%; height: 100%; background: linear-gradient(180deg, #2a2622 0%, #6b5a4c 55%, #25272d 100%); }

  .address { position: absolute; left: 160px; top: 305px; color: var(--white); font-size: 15px; line-height: 17.5px; }
  .contact { position: absolute; left: 158px; font-family: "Tinos", serif; color: var(--white); font-size: 15.5px; letter-spacing: -0.2px; display: flex; align-items: center; gap: 9px; white-space: nowrap; }
  .contact--phone { top: 368px; }
  .contact--web { top: 392px; }
  .contact-icon { width: 15px; height: 15px; flex: none; }
  .web-gold { color: var(--gold); }
  .web-stone { color: var(--stone); }
  .web-rust { color: var(--rust); }

  .footer-band { position: absolute; left: 0; bottom: 0; width: 100%; height: 17px; background: var(--gold); }

  /* back */
  .back-tile-field {
    position: absolute; inset: 0;
    background:
      radial-gradient(circle at 18% 20%, var(--tile-rust) 0%, transparent 38%),
      radial-gradient(circle at 82% 22%, var(--tile-slate) 0%, transparent 40%),
      radial-gradient(circle at 20% 82%, var(--tile-sage) 0%, transparent 40%),
      radial-gradient(circle at 80% 80%, var(--tile-gold) 0%, transparent 40%),
      radial-gradient(circle at 50% 50%, #161412 0%, #050505 75%);
  }
  .brand--back { left: 0; right: 0; top: 111px; flex-direction: column; gap: 40px; }
  .brand--back .brand-square { width: 120px; height: 120px; }
  .brand--back .brand-name { color: var(--white); font-size: 29px; letter-spacing: 0.14em; text-align: center; }
</style>
</head>
<body>

<section class="card card--front" aria-label="Business card front">
  <div class="brand brand--front">
    <div class="brand-square"></div>
    <p class="brand-name">QUARRYBEND<br>MARBLE &amp; TILE</p>
  </div>

  <div class="person">
    <h1 class="person-name">Dorian Fesslock</h1>
    <p class="person-title">Owner</p>
  </div>

  <div class="portrait">
    <div class="portrait-fill" role="img" aria-label="Portrait photo of Dorian Fesslock"></div>
  </div>

  <p class="address">24807 Hollis Verdant Blvd<br>Suite P &amp; R<br>Charlotte, NC 28193</p>

  <p class="contact contact--phone">
    <svg class="contact-icon" viewBox="0 0 16 16" aria-hidden="true">
      <path d="M1 5c2-3 12-3 14 0l-2 2-2.5-1.5V4H5.5v1.5L3 7z" fill="#d0922e"/>
      <rect x="3" y="8" width="10" height="6" rx="1" fill="#d0922e"/>
    </svg>
    704-583-7142
  </p>
  <p class="contact contact--web">
    <svg class="contact-icon" viewBox="0 0 16 16" aria-hidden="true">
      <circle cx="8" cy="8" r="7" fill="#d0922e"/>
      <path d="M5 3c2 1 1 3 3 3s1 3-1 3-1 3 0 5M11 4c-1 2 1 3 2 4" stroke="#000" stroke-width="1.3" fill="none"/>
    </svg>
    <span>www.<span class="web-gold">Quarrybend</span><span class="web-stone">Marble</span><span class="web-rust">And</span>Tile.com</span>
  </p>

  <div class="footer-band"></div>
</section>

<section class="card card--back" aria-label="Business card back">
  <div class="back-tile-field" role="img" aria-label="Repeating pattern of colourful mosaic tiles in rust, slate, sage and gold on black"></div>
  <div class="brand brand--back">
    <div class="brand-square"></div>
    <p class="brand-name">QUARRYBEND<br>MARBLE &amp; TILE</p>
  </div>
</section>

</body>
</html>
```